New & Improved KIVORA Business Card

I would like a two sided business card one side dedicated to home automation (security camera installation, television & sound bar mounting (hidden wires optional) , sink installation, fireplace mounting, chandelier installation and one side dedicated to all electronic repairs, In ex: plume band repairs, computer, zTab, laptop repairs, Velofon's, Korvex and etc.. Using the colors on this flyer. The phone number &email I want on both sides is (555) 214-3907 & Tech@Kivora.help. SAME COLOR AS THE FLYER ATTACHED.

Target Market(s)

EVERYONE.

Contact Information for Business Card

I would like a two sided business card one side dedicated to home automation (security camera installation, television & sound bar mounting (hidden wires optional) , sink installation, fireplace mounting, chandelier installation and one side dedicated to all electronic repairs, In ex: plume band repairs, computer, zTab, laptop repairs, Velofon's, Korvex and etc.. Using the colors on this flyer. The phone number &email I want on both sides is (555) 214-3907 & Tech@Kivora.help

Requirements
Must have
• -TV MOUNTING
-HOME AUTOMATION
-SECURITY CAMERA INSTALLATION
-ALL ELECTRONIC REPAIRS
- (555) 214-3907
-Tech@Kivora.help
-SAME COLOR AS THE FLYER
Nice to have
• Same colors & concept as the flyer attached below.
Should not have
• DO NOT DO A DIFF COLOR I WANT SAME COLOR AS THE FLYER ATTACHED.

```html
<!DOCTYPE html>
<html lang="en">
<head>
<meta charset="utf-8">
<title>KIVORA Business Card</title>
<link rel="stylesheet" href="https://fonts.googleapis.com/css2?family=Montserrat:wght@600;700&family=Nunito+Sans:wght@400&display=swap">
<style>
  :root {
    --pink: #ee2890;
    --blush: #f3dbe7;
    --paper: #f9f9f9;
    --ink: #1c1c1c;
    --backdrop: #e8e8e8;
    --white: #ffffff;
  }
  * { margin: 0; padding: 0; box-sizing: border-box; }
  html, body {
    width: 1200px;
    height: 801px;
    overflow: hidden;
    background: var(--backdrop);
  }
  .canvas {
    position: relative;
    width: 1200px;
    height: 801px;
  }
  .card {
    position: absolute;
    width: 594px;
    height: 340px;
  }
  .card--front {
    left: 126px;
    top: 22px;
    background: var(--paper);
  }
  .card--back {
    left: 529px;
    top: 425px;
    background: var(--pink);
  }
  .wordmark {
    position: absolute;
    left: 0;
    width: 100%;
    text-align: center;
    font-family: "Montserrat", sans-serif;
    font-weight: 600;
    font-size: 62px;
    line-height: 1;
    letter-spacing: 0.2em;
    text-indent: 0.2em;
  }
  .card--front .wordmark {
    top: 102px;
    color: var(--blush);
  }
  .card--back .wordmark {
    top: 145px;
    color: var(--white);
  }
  .services {
    position: absolute;
    left: 132px;
    width: 330px;
    top: 180px;
    font-family: "Montserrat", sans-serif;
    font-weight: 700;
    font-size: 11.2px;
    letter-spacing: 0.04em;
    color: var(--ink);
  }
  .services__row {
    display: flex;
    justify-content: space-between;
    align-items: center;
    height: 14px;
    margin-bottom: 11.5px;
    white-space: nowrap;
  }
  .services__sep { color: var(--pink); font-weight: 700; }
  .contact {
    position: absolute;
    left: 0;
    width: 100%;
    top: 291px;
    display: flex;
    justify-content: center;
    align-items: center;
    gap: 0;
    font-family: "Nunito Sans", sans-serif;
    font-weight: 400;
    font-size: 15.5px;
    letter-spacing: 0.08em;
    color: var(--ink);
    white-space: nowrap;
  }
  .contact__item { display: flex; align-items: center; }
  .contact__item--phone { margin-right: 14px; }
  .contact__icon { fill: var(--pink); display: block; }
  .contact__icon--phone { margin-right: 4px; }
  .contact__icon--mail { margin-right: 11px; }
</style>
</head>
<body>
<main class="canvas">
  <section class="card card--front" aria-label="Business card front">
    <h1 class="wordmark">KIVORA</h1>
    <div class="services">
      <p class="services__row">
        <span>TV MOUNTING</span><span class="services__sep">|</span><span>SECURITY CAMERA INSTALLATION</span>
      </p>
      <p class="services__row">
        <span>HOME AUTOMATION</span><span class="services__sep">|</span><span>ALL ELECTRONIC REPAIRS</span>
      </p>
    </div>
    <div class="contact">
      <span class="contact__item contact__item--phone">
        <svg class="contact__icon contact__icon--phone" width="16" height="17" viewBox="0 0 24 24" aria-hidden="true">
          <path d="M6.6 10.8c1.4 2.8 3.8 5.1 6.6 6.6l2.2-2.2c.3-.3.7-.4 1-.2 1.1.4 2.3.6 3.6.6.6 0 1 .4 1 1V20c0 .6-.4 1-1 1C10.6 21 3 13.4 3 4c0-.6.4-1 1-1h3.5c.6 0 1 .4 1 1 0 1.3.2 2.5.6 3.6.1.3 0 .7-.2 1l-2.3 2.2z"/>
        </svg>
        (555) 214-3907
      </span>
      <span class="contact__item">
        <svg class="contact__icon contact__icon--mail" width="20" height="14" viewBox="0 0 20 14" aria-hidden="true">
          <path d="M0 0h20v14H0z"/>
          <path d="M1 1l9 7 9-7" fill="none" stroke="#f9f9f9" stroke-width="1.6"/>
        </svg>
        Tech@Kivora.help
      </span>
    </div>
  </section>

  <section class="card card--back" aria-label="Business card back">
    <h2 class="wordmark">KIVORA</h2>
  </section>
</main>
</body>
</html>
```